BOLD & MINIMALIST DESIGN NEEDED

We want a very bold but minimalistic business card design that is impactful and utilizes both sides of the business card. Our current logo is included for your use.

We want bold fonts and good use of negative space. We don't want the logo to overpower the design.

Target Market(s)

Professionals who are building new commercial buildings.

Industry/Entity Type

Construction

Contact Information for Business Card

Name, Title, email, office phone, cell phone, website

Font styles to use
Serif
Sans Serif

Requirements
Must have
• Bold design!

```html
<!DOCTYPE html>
<html lang="en">
<head>
<meta charset="utf-8">
<title>Ridgeline Build – Business Card</title>
<link rel="stylesheet" href="https://fonts.googleapis.com/css2?family=Poppins:wght@300;400;500;700&display=swap">
<style>
  :root {
    --backdrop: #262626;
    --card: #2c2c2d;
    --card-edge: #3a3a3b;
    --ink: #f2f2f2;
    --ink-soft: #d6d6d6;
    --accent: #7ab929;
    --mark: #3b3b3d;
  }
  * { margin: 0; padding: 0; box-sizing: border-box; }
  html, body {
    width: 1200px; height: 576px; overflow: hidden;
    background: var(--backdrop);
    font-family: "Poppins", sans-serif;
  }
  .canvas { position: relative; width: 1200px; height: 576px; }
  .card {
    position: absolute; top: 138px;
    width: 486px; height: 294px;
    background: linear-gradient(160deg, #303031, var(--card) 60%, #262627);
    border-radius: 8px;
    box-shadow: 0 2px 6px rgba(0,0,0,.45);
    overflow: hidden;
  }
  .card--front { left: 102px; }
  .card--back { left: 598px; }

  .brand-name {
    position: absolute;
    font-weight: 700; color: var(--ink);
    letter-spacing: 1px; text-transform: uppercase;
    white-space: nowrap;
  }
  .card--front .brand-name { left: 48px; top: 124px; font-size: 27px; }
  .card--back .brand-name { right: 36px; top: 34px; font-size: 27px; }

  .brand-block {
    position: absolute; width: 150px; height: 150px;
    background: var(--mark); border-radius: 2px;
  }
  .card--front .brand-block { right: 30px; top: 72px; }
  .card--back .brand-block { left: 30px; top: 72px; }

  .person {
    position: absolute; right: 36px; top: 150px; text-align: right;
  }
  .person__name { font-size: 21px; font-weight: 500; color: var(--accent); line-height: 1.2; }
  .person__title { font-size: 11px; font-weight: 400; color: var(--ink-soft); margin-top: 4px; }

  .contact {
    position: absolute; right: 36px; top: 215px;
    list-style: none; text-align: right;
  }
  .contact__item {
    display: flex; justify-content: flex-end; align-items: center; gap: 7px;
    font-size: 12px; font-weight: 300; color: var(--ink-soft);
    line-height: 16.5px;
  }
  .contact__icon { width: 10px; height: 10px; fill: var(--accent); }
</style>
</head>
<body>
<main class="canvas">
  <section class="card card--front" aria-label="Card front">
    <div class="brand-name">Ridgeline Build</div>
    <div class="brand-block" aria-hidden="true"></div>
  </section>

  <section class="card card--back" aria-label="Card back">
    <div class="brand-block" aria-hidden="true"></div>
    <div class="brand-name">Ridgeline Build</div>

    <div class="person">
      <p class="person__name">Daniel Reyes</p>
      <p class="person__title">Director</p>
    </div>

    <ul class="contact">
      <li class="contact__item">555-014-0027
        <svg class="contact__icon" viewBox="0 0 10 10" aria-hidden="true"><path d="M1 3 Q5 0 9 3 L8 4.5 L6.5 3.8 L6.5 3 Q5 2.5 3.5 3 L3.5 3.8 L2 4.5Z M2.5 5 L7.5 5 L8.5 9 L1.5 9Z"/></svg>
      </li>
      <li class="contact__item">daniel@ridgelinebuild.com
        <svg class="contact__icon" viewBox="0 0 10 10" aria-hidden="true"><path d="M0.5 2 H9.5 V8 H0.5Z M1 2.5 L5 5.5 L9 2.5" stroke="#2c2c2d" stroke-width="0.8"/></svg>
      </li>
      <li class="contact__item">www.ridgelinebuild.com
        <svg class="contact__icon" viewBox="0 0 10 10" aria-hidden="true"><circle cx="5" cy="5" r="4.5"/><path d="M0.5 5 H9.5 M5 0.5 Q2.5 5 5 9.5 M5 0.5 Q7.5 5 5 9.5" fill="none" stroke="#2c2c2d" stroke-width="0.7"/></svg>
      </li>
    </ul>
  </section>
</main>
</body>
</html>
```